Consulting company business cards

We have a base design, but would be willing to update. We have a new logo/"tag" that needs to be added. Current business card design is attached for reference into our "style."

Industry/Entity Type

Business

Contact Information for Business Card

Should contain name and title, office number, mobile number if appropriate, e-mail, website, physical address, and company logo.

Font styles to use
Other font styles liked:
• See current card design on KorvandBCard

Colors
0455a3
85acd3
aaaaaa

Requirements
Must have
• Our colors are navy blue, gray, and a lighter blue
Nice to have
• Design that I can easily drop in new names/titles as we hire employees.

```html
<!DOCTYPE html>
<html lang="en">
<head>
<meta charset="utf-8">
<title>Brennick – Business Cards</title>
<link rel="stylesheet" href="https://fonts.googleapis.com/css2?family=Open+Sans:wght@300;400;600;700;800&display=swap">
<style>
  :root {
    --stage: #1c1c1c;
    --card-light: #f7f8fa;
    --card-navy: #0f3b5e;
    --ink-navy: #1d4466;
    --ink-blue: #2c5a86;
    --ink-grey: #8a8f96;
    --map-light: #dfe4ec;
    --map-navy: #1a4a70;
    --white: #ffffff;
  }
  * { box-sizing: border-box; margin: 0; padding: 0; }
  html, body { width: 1200px; height: 873px; overflow: hidden; }
  body {
    background: var(--stage);
    font-family: "Open Sans", sans-serif;
    position: relative;
  }
  .card {
    position: absolute;
    width: 540px;
    height: 309px;
    border-radius: 14px;
    overflow: hidden;
  }
  .card--front { left: 30px; top: 282px; background: var(--card-light); color: var(--ink-navy); }
  .card--back { left: 630px; top: 282px; background: var(--card-navy); color: var(--white); }

  .world-map {
    position: absolute;
    border-radius: 40% 45% 38% 42%;
  }
  .card--front .world-map {
    left: 150px; top: 40px; width: 330px; height: 190px;
    background: radial-gradient(ellipse at center, var(--map-light) 0%, rgba(223,228,236,0) 72%);
  }
  .card--back .world-map {
    left: 80px; top: 50px; width: 400px; height: 210px;
    background: radial-gradient(ellipse at center, var(--map-navy) 0%, rgba(26,74,112,0) 72%);
  }

  .brand { position: absolute; }
  .brand__name { font-weight: 800; letter-spacing: 1px; line-height: 1; }
  .brand__tag { font-weight: 400; letter-spacing: 2px; line-height: 1; }

  .card--front .brand { left: 30px; top: 38px; }
  .card--front .brand__name { font-size: 38px; color: var(--ink-navy); }
  .card--front .brand__tag { font-size: 10px; color: var(--ink-grey); margin-top: 5px; }

  .person { position: absolute; right: 30px; top: 40px; text-align: left; }
  .person__name { font-size: 20px; font-weight: 300; color: var(--ink-blue); }
  .person__name b { font-weight: 700; color: var(--ink-navy); }
  .person__title { font-size: 10px; color: var(--ink-grey); margin-top: 1px; }
  .rule { position: absolute; height: 1px; background: var(--ink-navy); }
  .rule--top { left: 270px; right: 30px; top: 92px; }
  .rule--bottom { left: 30px; width: 250px; top: 188px; }

  .contact { position: absolute; left: 30px; top: 200px; list-style: none; }
  .contact li {
    display: flex; align-items: center; gap: 10px;
    font-size: 14px; color: var(--ink-blue); height: 22px;
  }
  .contact svg { width: 14px; height: 14px; fill: var(--ink-navy); }
  .contact .address { font-weight: 700; color: var(--ink-navy); margin-top: 4px; }

  .card--back .brand { left: 50px; top: 95px; }
  .card--back .brand__name { font-size: 76px; color: var(--white); }
  .card--back .brand__tag { font-size: 19px; margin-top: 8px; letter-spacing: 2.5px; }
  .website {
    position: absolute; left: 0; right: 0; top: 245px;
    text-align: center; font-size: 16px; font-weight: 600; letter-spacing: 1.5px;
  }
</style>
</head>
<body>
  <section class="card card--front">
    <div class="world-map" role="img" aria-label="Faint dotted world map in light grey"></div>
    <div class="brand">
      <div class="brand__name">BRENNICK</div>
      <div class="brand__tag">A CLOUD CONSULTING COMPANY</div>
    </div>
    <div class="person">
      <div class="person__name">Dana <b>Korvand</b></div>
      <div class="person__title">Office Manager</div>
    </div>
    <div class="rule rule--top"></div>
    <div class="rule rule--bottom"></div>
    <ul class="contact">
      <li>
        <svg viewBox="0 0 16 16" aria-hidden="true"><path d="M2 5c0-2 2-3 6-3s6 1 6 3v1h-3V5H5v1H2zM4 7h8l2 6H2z"/></svg>
        555.014.2910
      </li>
      <li>
        <svg viewBox="0 0 16 16" aria-hidden="true"><path d="M4 1h8v4H4zM1 6h14v6h-3v3H4v-3H1zM5 10v4h6v-4z"/></svg>
        555.014.2971
      </li>
      <li>
        <svg viewBox="0 0 16 16" aria-hidden="true"><path d="M1 3h14v10H1zM2 4l6 5 6-5v1L8 10 2 5z" fill-rule="evenodd"/></svg>
        Dkorvand@Brennicktech.com
      </li>
      <li class="address">1180 W Lakeview Ave Springfield Ohio 45502</li>
    </ul>
  </section>

  <section class="card card--back">
    <div class="world-map" role="img" aria-label="Faint dotted world map in soft navy"></div>
    <div class="brand">
      <div class="brand__name">BRENNICK</div>
      <div class="brand__tag">A CLOUD CONSULTING COMPANY</div>
    </div>
    <div class="website">www.Brennicktech.com</div>
  </section>
</body>
</html>
```